Online business manager needs a website

I need a website designed and then coded. I am an online business manager serving a number of different industries providing administrative support to existing small businesses and helping solo practitioners get their new business up and running.

I didn't have a logo formally designed but have been using the attached avatar and wouldn't mind something that incorporated that.

The business doesn't have an official name, so I've just been using my name Lena Morvath, Online Business Manager or Lena Morvath, OBM. I've attached two documents that I have made previously for an example of content.

I would prefer the final site be in Wordpress.

Requirements
Must have
• A way to contact me, testimonials, list of services

```html
<!DOCTYPE html>
<html lang="en">
<head>
<meta charset="utf-8">
<title>Lena Morvath, Online Business Manager</title>
<link href="https://fonts.googleapis.com/css2?family=Alegreya+Sans:ital,wght@1,700;1,800&family=Poppins:wght@400;500;600&display=swap" rel="stylesheet">
<style>
:root{
  --purple:#4b1a7d;
  --purple-mid:#6a3a9e;
  --lilac:#a17ccd;
  --lilac-soft:#b896dc;
  --ink:#222;
  --grey:#555;
  --white:#fff;
  --star:#f5c518;
}
*{box-sizing:border-box;margin:0;padding:0}
html,body{width:1200px;height:4095px;overflow:hidden}
body{font-family:"Poppins",sans-serif;color:var(--ink);background:var(--white);position:relative}
.abs{position:absolute}
.display{font-family:"Alegreya Sans",sans-serif;font-style:italic;font-weight:800}
.center{text-align:center}

/* header */
.site-header{left:0;top:0;width:1200px;height:84px;background:var(--white)}
.brand-mark{left:111px;top:25px;width:34px;height:34px;border-radius:50%;background:var(--lilac)}
.brand-name{left:157px;top:26px;font-family:"Poppins",sans-serif;font-size:22px;font-weight:600;line-height:32px;color:var(--purple);white-space:nowrap}
.nav{top:31px;font-size:15px;color:#333}
.nav.active{color:var(--purple-mid)}

/* hero */
.hero{left:0;top:84px;width:1200px;height:639px;background:linear-gradient(120deg,#3e3a36 0%,#6b4a3e 40%,#8a5a48 55%,#4a3c38 100%)}
.hero-shade{left:0;top:84px;width:1200px;height:639px;background:rgba(20,10,30,.45)}
.hero-welcome{left:0;top:238px;width:1200px;font-size:40px;color:var(--white)}
.hero-title{left:0;top:285px;width:1200px;font-size:53px;font-weight:600;color:var(--white)}
.hero-text{left:245px;top:374px;width:710px;font-size:15.5px;line-height:26px;color:var(--white)}
.btn{display:block;border-radius:22px;font-size:15px;text-align:center;line-height:42px;height:42px}
.btn-light{background:var(--white);color:var(--purple)}
.btn-dark{background:var(--purple);color:var(--white)}
.dot{width:7px;height:7px;border-radius:50%;background:rgba(255,255,255,.6);top:652px}

/* section titles */
.section-title{left:0;width:1200px;font-size:40px;color:var(--purple)}

/* services */
.svc{width:260px;text-align:center}
.svc-icon{width:100px;height:100px;margin:0 auto}
.svc-name{font-size:21px;line-height:30px;color:var(--ink);margin-top:16px}
.svc-list{font-size:15px;line-height:26px;color:var(--grey);margin-top:16px;white-space:nowrap}
.svc .btn{width:124px;margin:32px auto 0}

/* about */
.about-band{left:0;top:1338px;width:687px;height:448px;background:var(--purple)}
.about-photo{left:687px;top:1338px;width:513px;height:448px;background:radial-gradient(circle at 50% 50%,#e8c0a8 0%,#c98aa0 30%,#a2406e 60%,#4f6a2c 100%)}
.about-title{left:111px;top:1385px;font-size:40px;color:var(--white)}
.about-text{left:111px;top:1452px;width:510px;font-size:15px;line-height:26px;color:var(--white)}
.about-text p+p{margin-top:17px}

/* best */
.best{width:250px;text-align:center}
.best svg{display:block;margin:0 auto}
.best-label{font-size:21px;color:var(--ink);margin-top:8px}

/* testimonials */
.love{left:0;top:2347px;width:1200px;height:380px;background:linear-gradient(90deg,#2c3140 0%,#555a66 40%,#6a6a72 60%,#3a3e4a 100%)}
.love-shade{left:0;top:2347px;width:1200px;height:380px;background:rgba(25,30,45,.55)}
.love-title{left:0;top:2380px;width:1200px;font-size:40px;color:var(--white)}
.love-text{left:330px;top:2444px;width:540px;font-size:15.5px;line-height:26px;color:var(--white)}
.love-name{left:0;top:2562px;width:1200px;font-family:Georgia,serif;font-style:italic;font-weight:700;font-size:14px;color:var(--white)}
.quote{font-family:Georgia,serif;font-size:56px;color:var(--white);line-height:1}

/* my work */
.work-back{left:203px;top:2814px;width:418px;height:412px;background:var(--purple);border-radius:18px}
.work-photo{left:111px;top:2836px;width:491px;height:485px;border-radius:14px;background:linear-gradient(135deg,#6b5a4a 0%,#c99a6e 35%,#e3b890 50%,#8a8a8a 80%,#4a4a4a 100%)}
.work-title{left:674px;top:2853px;font-size:40px;color:var(--purple)}
.work-text{left:674px;top:2930px;width:430px;font-size:15px;line-height:26px;color:var(--grey)}
.work-text p+p{margin-top:26px}

/* contact */
.contact{left:0;top:3410px;width:1200px;height:610px;background:linear-gradient(100deg,#4a1f78 0%,#6a3a9a 50%,#5a2a88 100%)}
.contact-title{left:111px;top:3466px;font-size:39px;line-height:42px;color:var(--white)}
.contact-text{left:111px;top:3585px;width:520px;font-size:15px;line-height:26px;color:var(--white)}
.contact-line{left:111px;font-size:34px;color:var(--white);display:flex;align-items:center;gap:20px}
.contact-line svg{flex:none}
.form-card{left:710px;top:3475px;width:378px;height:467px;background:var(--lilac);border-radius:28px}
.form-title{left:710px;top:3510px;width:378px;font-size:40px;color:var(--white)}
.field{left:731px;width:337px;background:var(--white);font-size:15px;color:#555;padding:12px 12px}

/* footer */
.footer{left:0;top:4020px;width:1200px;height:75px;background:#0f0f0f;color:var(--white)}
.footer-copy{left:111px;font-size:13.5px;color:var(--white)}
.footer-links{left:961px;font-size:15.5px;color:var(--white)}
.foot-box{width:22px;height:22px;background:var(--white);border-radius:3px}
</style>
</head>
<body>

<header class="abs site-header">
  <span class="abs brand-mark"></span>
  <div class="abs brand-name">Lena Morvath, OBM</div>
  <span class="abs nav active" style="left:535px">Home</span>
  <span class="abs nav" style="left:610px">About Me</span>
  <span class="abs nav" style="left:712px">Services</span>
  <span class="abs nav" style="left:804px">Testimonials</span>
  <span class="abs nav" style="left:930px">Contact Me</span>
  <svg class="abs" style="left:1058px;top:27px" width="30" height="30" viewBox="0 0 30 30"><circle cx="12" cy="12" r="9" fill="none" stroke="#4b1a7d" stroke-width="3"/><line x1="19" y1="19" x2="28" y2="28" stroke="#4b1a7d" stroke-width="3.5" stroke-linecap="round"/></svg>
</header>

<section>
  <div class="abs hero" role="img" aria-label="Photo of a woman working at a laptop in a bright office"></div>
  <div class="abs hero-shade"></div>
  <div class="abs hero-welcome display center">Welcome to&nbsp; Lena Morvath</div>
  <h1 class="abs hero-title center">Online Business Manager</h1>
  <p class="abs hero-text center">Lorem ipsum dolor sit amet, consectetur adipiscing elit, sed do eiusmod tempor incididunt ut labore et dolore magna aliqua. Ut enim ad minim veniam, quis nostrud exercitation ullamco laboris nisi ut aliquip ex ea commodo consequat.</p>
  <a class="abs btn btn-light" style="left:538px;top:480px;width:124px">Contact Me</a>
  <span class="abs dot" style="left:575px;background:#fff"></span>
  <span class="abs dot" style="left:587px"></span>
  <span class="abs dot" style="left:597px"></span>
  <span class="abs dot" style="left:607px"></span>
  <span class="abs dot" style="left:617px"></span>
</section>

<section>
  <h2 class="abs section-title display center" style="top:797px">About Services</h2>

  <div class="abs svc" style="left:88px;top:908px">
    <svg class="svc-icon" viewBox="0 0 100 100"><rect x="10" y="10" width="80" height="58" rx="4" fill="#a17ccd" stroke="#4b1a7d" stroke-width="3"/><rect x="5" y="68" width="90" height="8" rx="3" fill="none" stroke="#4b1a7d" stroke-width="3"/><circle cx="40" cy="40" r="10" fill="none" stroke="#4b1a7d" stroke-width="3"/><path d="M24 68c2-12 30-12 32 0" fill="none" stroke="#4b1a7d" stroke-width="3"/><rect x="56" y="18" width="26" height="16" rx="3" fill="#fff" stroke="#4b1a7d" stroke-width="2.5"/></svg>
    <div class="svc-name display">Virtual<br>Assistance</div>
    <div class="svc-list">Calendar Management<br>Email Management<br>Light Graphic Design<br>Data Entry</div>
    <a class="btn btn-dark">Learn More</a>
  </div>

  <div class="abs svc" style="left:342px;top:908px">
    <svg class="svc-icon" viewBox="0 0 100 100"><circle cx="50" cy="48" r="32" fill="#a17ccd"/><g fill="#fff" stroke="#4b1a7d" stroke-width="3"><circle cx="50" cy="48" r="10"/><circle cx="24" cy="24" r="9"/><circle cx="78" cy="24" r="9"/><circle cx="20" cy="62" r="9"/><circle cx="80" cy="62" r="9"/><circle cx="50" cy="86" r="9"/></g></svg>
    <div class="svc-name display">Social Media &amp;<br>Content Management</div>
    <div class="svc-list">Content Repurposing<br>Graphics Creation<br>Audiogram Creation<br>Search Engine Optimization</div>
    <a class="btn btn-dark">Learn More</a>
  </div>

  <div class="abs svc" style="left:596px;top:908px">
    <svg class="svc-icon" viewBox="0 0 100 100"><circle cx="44" cy="52" r="30" fill="#a17ccd"/><circle cx="52" cy="48" r="26" fill="none" stroke="#4b1a7d" stroke-width="7" stroke-dasharray="9 6"/><circle cx="52" cy="48" r="10" fill="none" stroke="#4b1a7d" stroke-width="4"/><circle cx="24" cy="72" r="12" fill="#fff" stroke="#4b1a7d" stroke-width="3"/><text x="24" y="78" font-size="16" text-anchor="middle" fill="#4b1a7d" font-family="Poppins,sans-serif">$</text></svg>
    <div class="svc-name display">Finance<br>Management</div>
    <div class="svc-list">Create Invoices<br>Track Receivables<br>Analyze Expenses<br>Year Over Year Analytics</div>
    <a class="btn btn-dark">Learn More</a>
  </div>

  <div class="abs svc" style="left:850px;top:908px">
    <svg class="svc-icon" viewBox="0 0 100 100"><circle cx="50" cy="40" r="30" fill="#a17ccd"/><circle cx="50" cy="34" r="22" fill="none" stroke="#4b1a7d" stroke-width="6" stroke-dasharray="8 6"/><path d="M10 48l20 30 20-12 20 12 20-30" fill="none" stroke="#4b1a7d" stroke-width="3.5" stroke-linejoin="round"/><path d="M36 66l14-10 14 10" fill="none" stroke="#4b1a7d" stroke-width="3"/></svg>
    <div class="svc-name display">Business<br>Management</div>
    <div class="svc-list">Creation of Operating Procedures<br>Review of Website Strategy<br>Reporting and Analytics<br>Project Management</div>
    <a class="btn btn-dark">Learn More</a>
  </div>
</section>

<section>
  <div class="abs about-band"></div>
  <div class="abs about-photo" role="img" aria-label="Portrait of Lena Morvath in front of pink flowering shrubs"></div>
  <h2 class="abs about-title display">About Me</h2>
  <div class="abs about-text">
    <p>Hi! I'm so excited that you have chosen to explore my portfolio. Helping businesses achieve their goals is my passion, and I'm thrilled that with my assistance you will have more time for your own passion project.</p>
    <p>I thrive while working independently, which means you can be confident when leaving tasks for me. The type of work that lights me up is anything involving organization and/or spreadsheets.</p>
  </div>
  <a class="abs btn btn-light" style="left:111px;top:1686px;width:126px">Read More</a>
</section>

<section>
  <h2 class="abs section-title display center" style="top:1862px">What I Do Best</h2>

  <div class="abs best" style="left:86px;top:1958px"><svg width="120" height="92" viewBox="0 0 120 92"><circle cx="48" cy="46" r="40" fill="#a17ccd"/><rect x="42" y="12" width="44" height="60" rx="3" fill="#fff" stroke="#4b1a7d" stroke-width="3" transform="rotate(12 64 42)"/><g stroke="#4b1a7d" stroke-width="3"><line x1="54" y1="30" x2="78" y2="35"/><line x1="52" y1="42" x2="76" y2="47"/><line x1="50" y1="54" x2="70" y2="58"/><line x1="96" y1="14" x2="78" y2="62"/></g></svg><div class="best-label display">Content Repurposing</div></div>

  <div class="abs best" style="left:337px;top:1958px"><svg width="120" height="92" viewBox="0 0 120 92"><circle cx="46" cy="46" r="40" fill="#a17ccd"/><rect x="38" y="8" width="42" height="58" rx="3" fill="#fff" stroke="#4b1a7d" stroke-width="3"/><rect x="30" y="46" width="72" height="30" rx="3" fill="none" stroke="#4b1a7d" stroke-width="3"/><g stroke="#4b1a7d" stroke-width="3"><line x1="46" y1="22" x2="72" y2="22"/><line x1="46" y1="32" x2="72" y2="32"/></g></svg><div class="best-label display">Data Entry</div></div>

  <div class="abs best" style="left:604px;top:1958px"><svg width="120" height="92" viewBox="0 0 120 92"><circle cx="46" cy="46" r="40" fill="#a17ccd"/><rect x="36" y="30" width="74" height="50" rx="3" fill="none" stroke="#4b1a7d" stroke-width="3"/><path d="M36 30l37 28 37-28" fill="none" stroke="#4b1a7d" stroke-width="3"/><circle cx="73" cy="26" r="12" fill="#fff" stroke="#4b1a7d" stroke-width="3"/></svg><div class="best-label display">Email Management</div></div>

  <div class="abs best" style="left:865px;top:1958px"><svg width="120" height="92" viewBox="0 0 120 92"><circle cx="46" cy="46" r="40" fill="#a17ccd"/><circle cx="84" cy="30" r="16" fill="none" stroke="#4b1a7d" stroke-width="6" stroke-dasharray="6 4"/><path d="M52 36a16 16 0 1 1 0 30v8h-14v-8a16 16 0 0 1 14-30z" fill="#fff" stroke="#4b1a7d" stroke-width="3"/></svg><div class="best-label display">Project Management</div></div>

  <div class="abs best" style="left:77px;top:2132px"><svg width="120" height="92" viewBox="0 0 120 92"><circle cx="46" cy="48" r="40" fill="#a17ccd"/><g fill="none" stroke="#4b1a7d" stroke-width="3"><rect x="40" y="56" width="10" height="26"/><rect x="56" y="44" width="10" height="38"/><rect x="72" y="36" width="10" height="46"/><rect x="88" y="26" width="10" height="56"/><path d="M30 54l26-20 16 8 30-30"/><circle cx="52" cy="74" r="10" fill="#fff"/></g></svg><div class="best-label display">Financial Analytics</div></div>

  <div class="abs best" style="left:339px;top:2132px"><svg width="120" height="92" viewBox="0 0 120 92"><circle cx="48" cy="48" r="40" fill="#a17ccd"/><circle cx="46" cy="30" r="14" fill="#fff" stroke="#4b1a7d" stroke-width="3"/><circle cx="82" cy="44" r="20" fill="none" stroke="#4b1a7d" stroke-width="3"/><path d="M82 34v20M72 44h20M66 58l-26 26" stroke="#4b1a7d" stroke-width="3"/></svg><div class="best-label display">Graphic Creations</div></div>

  <div class="abs best" style="left:598px;top:2132px"><svg width="120" height="92" viewBox="0 0 120 92"><circle cx="46" cy="46" r="40" fill="#a17ccd"/><rect x="42" y="14" width="40" height="62" rx="3" fill="#fff" stroke="#4b1a7d" stroke-width="3"/><rect x="70" y="40" width="34" height="44" rx="3" fill="#fff" stroke="#4b1a7d" stroke-width="3"/><text x="56" y="46" font-size="20" fill="#4b1a7d" font-family="Poppins,sans-serif">$</text><g fill="#4b1a7d"><rect x="76" y="50" width="22" height="8"/><rect x="76" y="64" width="6" height="6"/><rect x="86" y="64" width="6" height="6"/><rect x="76" y="74" width="6" height="6"/><rect x="86" y="74" width="6" height="6"/></g></svg><div class="best-label display">Bookkeeping</div></div>

  <div class="abs best" style="left:868px;top:2132px"><svg width="120" height="92" viewBox="0 0 120 92"><circle cx="48" cy="46" r="40" fill="#a17ccd"/><g fill="none" stroke="#4b1a7d" stroke-width="3.5"><rect x="46" y="18" width="24" height="24" rx="6"/><rect x="76" y="18" width="24" height="24" rx="6"/><rect x="46" y="50" width="24" height="24" rx="6"/><circle cx="88" cy="62" r="12"/></g></svg><div class="best-label display">More Awesomeness</div></div>
</section>

<section>
  <div class="abs love" role="img" aria-label="Photo of colleagues smiling during a meeting in an office"></div>
  <div class="abs love-shade"></div>
  <h2 class="abs love-title display center">Client Love</h2>
  <span class="abs quote" style="left:284px;top:2438px">&#8220;</span>
  <p class="abs love-text center">When it became apparent that a project would take more time than I had, Lena stepped up to take on the required research. She was thorough and timely; able to meet a last-minute 12-hour deadline. I would highly recommend Lena to assist with your next project.</p>
  <span class="abs quote" style="left:848px;top:2524px">&#8221;</span>
  <div class="abs love-name center">Dana R. Owner, Summit Ridge Roofing</div>
  <div class="abs center" style="left:0;top:2590px;width:1200px;font-size:14px;color:var(--star);letter-spacing:1px">&#9733;&#9733;&#9733;&#9733;&#9733;</div>
  <span class="abs" style="left:576px;top:2680px;width:12px;height:4px;background:#a17ccd;border-radius:2px"></span>
  <span class="abs" style="left:592px;top:2680px;width:12px;height:4px;background:#fff;border-radius:2px"></span>
  <span class="abs" style="left:608px;top:2680px;width:12px;height:4px;background:#fff;border-radius:2px"></span>
</section>

<section>
  <div class="abs work-back"></div>
  <div class="abs work-photo" role="img" aria-label="Smiling portrait of Lena Morvath on a city street"></div>
  <h2 class="abs work-title display">My Work</h2>
  <div class="abs work-text">
    <p>Sed ut perspiciatis unde omnis iste natus error sit voluptatem accusantium doloremque laudantium, totam rem aperiam, eaque ipsa quae ab illo inventore veritatis et quasi architecto beatae vitae dicta sunt explicabo.</p>
    <p>Duis aute irure dolor in reprehenderit in voluptate velit esse cillum dolore eu fugiat nulla pariatur. Excepteur sint occaecat cupidatat non proident, sunt in culpa qui officia deserunt mollit anim id est laborum."</p>
  </div>
  <a class="abs btn btn-dark" style="left:675px;top:3222px;width:124px">Read More</a>
</section>

<section>
  <div class="abs contact" role="img" aria-label="Soft purple-tinted photo of a woman holding a phone"></div>
  <h2 class="abs contact-title display">Need More Information<br>Get In Touch</h2>
  <p class="abs contact-text">Lorem ipsum dolor sit amet, consectetur adipiscing elit, sed do eiusmod tempor incididunt ut labore et dolore magna aliqua. Ut enim ad minim veniam, quis nostrud exercitation ullamco laboris nisi ut aliquip ex ea commodo consequat.</p>

  <div class="abs contact-line display" style="top:3714px"><svg width="22" height="22" viewBox="0 0 24 24"><path d="M6.6 10.8a15 15 0 0 0 6.6 6.6l2.2-2.2a1 1 0 0 1 1-.25 11.4 11.4 0 0 0 3.6.57 1 1 0 0 1 1 1V20a1 1 0 0 1-1 1A17 17 0 0 1 3 4a1 1 0 0 1 1-1h3.5a1 1 0 0 1 1 1c0 1.25.2 2.45.57 3.57a1 1 0 0 1-.25 1z" fill="#fff"/></svg>555.014.2286</div>
  <div class="abs contact-line display" style="top:3775px"><svg width="22" height="22" viewBox="0 0 24 24"><rect x="2" y="5" width="20" height="14" fill="#fff"/><path d="M2 5l10 8 10-8" fill="none" stroke="#5a2a88" stroke-width="2"/></svg>lena.morvath@mailbox.test</div>
  <div class="abs contact-line display" style="top:3835px"><span style="display:inline-block;width:20px;height:20px;background:#fff;border-radius:2px"></span>Lena Morvath OBM</div>
  <div class="abs contact-line display" style="top:3895px"><span style="display:inline-block;width:20px;height:20px;background:#fff;border-radius:2px"></span>/LenaMorvath07</div>

  <div class="abs form-card"></div>
  <div class="abs form-title display center">Contact Me</div>
  <div class="abs field" style="top:3580px;height:46px">Name</div>
  <div class="abs field" style="top:3640px;height:46px">Email</div>
  <div class="abs field" style="top:3701px;height:46px">Phone</div>
  <div class="abs field" style="top:3761px;height:73px">Message</div>
  <a class="abs btn btn-dark" style="left:853px;top:3859px;width:93px">Send</a>
</section>

<footer class="abs footer">
  <div class="abs footer-copy" style="top:28px">Copyright © 2023 Lena Morvath, Online Business Manager .</div>
  <span class="abs foot-box" style="left:664px;top:27px"></span>
  <span class="abs foot-box" style="left:708px;top:27px"></span>
  <span class="abs foot-box" style="left:752px;top:27px"></span>
  <div class="abs footer-links" style="top:26px">Terms&nbsp; | &nbsp;Privacy</div>
</footer>

</body>
</html>
```